Custom unique Stationary design for Logistics company

We need a custom, unique , elegant and luxurious full stationary design using our new logo, following these guidelines:
1- Business card: double sided, both sides uses the navy blue as the background main color (same as the code of the navy blue used in our logo).
2- envelope and folder: also use the same navy blue as the main background color.
3- book cover( notepad cover) : same thing with the navy blue
4- letterhead: feel free to use the combination of the colors in our logo.
5- rest of the items are up to your creativity

Target Market(s)

corporates and other businesses

Industry/Entity Type

Logistics and heavy machines contractors

Requirements
Must have
• Letterhead, business card, envelope, notepad cover, paper, file
Nice to have
• navy blue to be main background color for business card, envelope, notepad cover

```html
<!DOCTYPE html>
<html lang="en">
<head>
<meta charset="utf-8">
<title>Meridian Freight Group — Stationery</title>
<link href="https://fonts.googleapis.com/css2?family=Montserrat:wght@600;700&family=Open+Sans:wght@400;600&display=swap" rel="stylesheet">
<style>
:root{
  --navy:#1d4f73;
  --navy-dark:#163f5e;
  --orange:#e8602c;
  --paper:#ffffff;
  --ink:#3a3f45;
  --muted:#7c8690;
  --stage:#d9dbdd;
  --stage-warm:#e6e1db;
}
*{margin:0;padding:0;box-sizing:border-box}
html,body{width:1200px;height:5326px;overflow:hidden}
body{position:relative;font-family:"Open Sans",sans-serif;color:var(--ink);background:var(--stage)}
.section{position:absolute;left:0;width:1200px}
.s-cards{top:0;height:895px;background:var(--stage-warm)}
.s-letter{top:895px;height:1250px;background:var(--stage)}
.s-set{top:2145px;height:1410px;background:#d4d6d8}
.s-folder{top:3555px;height:890px;background:linear-gradient(#cfd2d4,#eceeef)}
.s-notebook{top:4445px;height:881px;background:#ebedee}
.abs{position:absolute}
.brand{font-family:"Montserrat",sans-serif;font-weight:700;color:var(--navy);letter-spacing:.5px;line-height:1.1;white-space:nowrap}
.brand.light{color:#fff}
.band{position:absolute;left:0;right:0;bottom:0;height:12px;
  background:linear-gradient(100deg,var(--navy) 0 66%,var(--paper) 66% 67%,var(--orange) 67% 100%)}
.shadow{box-shadow:0 8px 22px rgba(0,0,0,.22)}

/* business cards */
.card{width:520px;height:296px;border-radius:4px}
.card-front{left:60px;top:300px;background:var(--paper);border-bottom:10px solid var(--orange)}
.card-back{left:620px;top:300px;background:var(--navy);border-bottom:10px solid var(--navy-dark);display:flex;align-items:center;justify-content:center}
.card-front .brand{right:32px;top:34px;font-size:24px;text-align:right}
.card-front .rule{right:32px;top:100px;width:300px;height:2px;background:var(--orange)}
.card-front .address{right:32px;top:114px;text-align:right;font-size:13px;line-height:1.5}
.card-front .person{left:32px;top:166px}
.person-name{font-family:"Montserrat",sans-serif;font-weight:700;font-size:19px;color:var(--navy);letter-spacing:.5px}
.person-role{font-size:13px;color:var(--orange);font-weight:600;margin-bottom:8px}
.contact{font-size:12.5px;line-height:1.6;display:flex;align-items:center;gap:7px;white-space:nowrap}
.contact svg{width:12px;height:12px;fill:var(--navy);flex:none}
.card-back .brand{font-size:36px}

/* letterhead */
.letterhead{left:230px;top:175px;width:645px;height:895px;background:var(--paper)}
.letterhead .brand{left:58px;top:72px;font-size:26px}
.letterhead .head-contact{left:408px;top:56px;font-size:12.5px;line-height:1.45}
.head-contact .contact{font-size:12.5px;line-height:1.45}
.head-contact .contact svg{fill:var(--orange)}
.letter-body{left:58px;top:215px;width:530px;font-size:11.2px;line-height:1.55;color:#4a5058}
.letter-body p{margin-bottom:14px}
.signature{left:58px;top:680px;width:80px;height:60px;background:rgba(40,40,40,.06);border-radius:4px}
.letterhead .band{height:14px}

/* stationery set */
.sheet{background:var(--paper)}
.sheet .brand{font-size:17px}
.sheet .tiny{font-size:8.5px;line-height:1.35;color:var(--muted);margin-top:6px;text-align:center}
.sheet-head{position:absolute;left:44px;top:40px;text-align:center}
.envelope{background:var(--paper);overflow:hidden}
.flap{position:absolute;left:0;right:0;top:0;height:80px;background:var(--navy);
  clip-path:polygon(0 0,100% 0,100% 55%,90% 100%,10% 100%,0 55%)}
.flap .brand{position:absolute;left:0;right:0;top:24px;text-align:center;font-size:15px;color:#fff}

/* folder */
.folder-back{left:120px;top:150px;width:470px;height:560px;background:var(--navy)}
.folder-back .tiny{position:absolute;left:0;right:0;bottom:80px;text-align:center;color:#cfe0ec;font-size:10px;line-height:1.5}
.folder-front{left:590px;top:150px;width:470px;height:560px;background:var(--paper)}
.folder-front .brand{position:absolute;left:0;right:0;top:230px;text-align:center;font-size:32px}
.folder-front .web{position:absolute;right:30px;bottom:26px;font-size:10px;letter-spacing:2px;color:var(--navy);font-weight:600}
.folder-front .band{height:14px}

/* notebook */
.notebook-open{left:120px;top:180px;width:560px;height:380px;display:flex}
.page{flex:1;background:var(--paper);position:relative;border:1px solid #d6d9dc}
.page .brand{position:absolute;left:30px;top:28px;font-size:13px}
.notebook-cover{left:760px;top:150px;width:330px;height:440px;background:var(--navy);border-radius:3px 10px 10px 3px}
.notebook-cover .brand{position:absolute;left:0;right:0;top:170px;text-align:center;font-size:24px}
.elastic{position:absolute;top:0;bottom:0;right:40px;width:10px;background:#e8ecef}
.notebook-cover .web{position:absolute;left:28px;bottom:28px;font-size:9px;color:#cfe0ec;letter-spacing:1px}
</style>
</head>
<body>

<section class="section s-cards">
  <div class="abs card card-front shadow">
    <div class="abs brand">Meridian Freight Group</div>
    <div class="abs rule"></div>
    <div class="abs address">Meridian Freight Group<br>48 Harbor Lane, Suite 210<br>Portview, ST 10001</div>
    <div class="abs person">
      <div class="person-name">MARTIN KESSLER</div>
      <div class="person-role">Managing Director</div>
      <div class="contact"><svg viewBox="0 0 24 24"><path d="M6.6 10.8a15 15 0 0 0 6.6 6.6l2.2-2.2c.3-.3.7-.4 1-.2 1.1.4 2.3.6 3.6.6.6 0 1 .4 1 1V20c0 .6-.4 1-1 1A17 17 0 0 1 3 4c0-.6.4-1 1-1h3.5c.6 0 1 .4 1 1 0 1.2.2 2.4.6 3.6.1.3 0 .7-.2 1z"/></svg>555-010-2741</div>
      <div class="contact"><svg viewBox="0 0 24 24"><path d="M2 5h20v14H2z"/></svg>info@meridianfreight.example</div>
      <div class="contact"><svg viewBox="0 0 24 24"><circle cx="12" cy="12" r="10"/></svg>www.meridianfreight.example</div>
    </div>
  </div>
  <div class="abs card card-back shadow">
    <div class="brand light">Meridian Freight Group</div>
  </div>
</section>

<section class="section s-letter">
  <div class="abs letterhead shadow">
    <div class="abs brand">Meridian Freight Group</div>
    <div class="abs head-contact">
      75 Beacon Road<br>Lakeview, ON X0X 0A0
      <div class="contact"><svg viewBox="0 0 24 24"><path d="M6.6 10.8a15 15 0 0 0 6.6 6.6l2.2-2.2c.3-.3.7-.4 1-.2 1.1.4 2.3.6 3.6.6.6 0 1 .4 1 1V20c0 .6-.4 1-1 1A17 17 0 0 1 3 4c0-.6.4-1 1-1h3.5c.6 0 1 .4 1 1 0 1.2.2 2.4.6 3.6.1.3 0 .7-.2 1z"/></svg>555-010-4418</div>
      <div class="contact"><svg viewBox="0 0 24 24"><path d="M2 5h20v14H2z"/></svg>info@meridianfreight.example</div>
      <div class="contact"><svg viewBox="0 0 24 24"><circle cx="12" cy="12" r="10"/></svg>www.meridianfreight.example</div>
    </div>
    <div class="abs letter-body">
      <p>Dear customer,</p>
      <p>Lorem ipsum dolor sit amet, consectetur adipisicing elit, sed do eiusmod tempor incididunt ut labore et dolore magna aliqua. Ut enim ad minim veniam, quis nostrud exercitation ullamco laboris nisi ut aliquip ex ea commodo consequat. Duis aute irure dolor in reprehenderit in voluptate velit esse cillum dolore eu fugiat nulla pariatur. Excepteur sint occaecat cupidatat non proident, sunt in culpa qui officia deserunt mollit anim id est laborum.</p>
      <p>Lorem ipsum dolor sit amet, consectetur adipisicing elit, sed do eiusmod tempor incididunt ut labore et dolore magna aliqua. Ut enim ad minim veniam, quis nostrud exercitation ullamco laboris nisi ut aliquip ex ea commodo consequat. Duis aute irure dolor in reprehenderit in voluptate velit esse cillum dolore eu fugiat nulla pariatur. Excepteur sint occaecat cupidatat non proident, sunt in culpa qui officia deserunt mollit anim id est laborum.</p>
      <p>Lorem ipsum dolor sit amet, consectetur adipisicing elit, sed do eiusmod tempor incididunt ut labore et dolore magna aliqua. Ut enim ad minim veniam, quis nostrud exercitation ullamco laboris nisi ut aliquip ex ea commodo consequat. Duis aute irure dolor in reprehenderit in voluptate velit esse cillum dolore eu fugiat nulla pariatur. Excepteur sint occaecat cupidatat non proident, sunt in culpa qui officia deserunt mollit anim id est laborum.</p>
      <p>Lorem ipsum dolor sit amet, consectetur adipisicing elit, sed do eiusmod tempor incididunt ut labore et dolore magna aliqua. Ut enim ad minim veniam, quis nostrud exercitation ullamco laboris nisi ut aliquip ex ea commodo consequat. Duis aute irure dolor in reprehenderit.</p>
      <p>Yours Sincerely,</p>
    </div>
    <div class="abs signature" role="img" aria-label="Handwritten signature"></div>
    <div class="band"></div>
  </div>
</section>

<section class="section s-set">
  <div class="abs sheet shadow" style="left:137px;top:80px;width:440px;height:625px">
    <div class="sheet-head"><div class="brand">Meridian Freight Group</div><div class="tiny">48 Harbor Lane, Suite 210<br>Portview, ST 10001</div></div>
    <div class="band"></div>
  </div>
  <div class="abs envelope shadow" style="left:617px;top:80px;width:440px;height:625px">
    <div class="flap"><div class="brand">Meridian Freight Group</div></div>
  </div>

  <div class="abs sheet shadow" style="left:137px;top:735px;width:444px;height:325px">
    <div class="sheet-head"><div class="brand">Meridian Freight Group</div><div class="tiny">48 Harbor Lane, Suite 210<br>Portview, ST 10001</div></div>
    <div class="band"></div>
  </div>
  <div class="abs envelope shadow" style="left:613px;top:735px;width:444px;height:325px">
    <div class="flap"><div class="brand">Meridian Freight Group</div></div>
  </div>

  <div class="abs sheet shadow" style="left:137px;top:1070px;width:446px;height:210px">
    <div class="sheet-head" style="top:28px"><div class="brand">Meridian Freight Group</div><div class="tiny">48 Harbor Lane, Suite 210<br>Portview, ST 10001</div></div>
    <div class="band"></div>
  </div>
  <div class="abs envelope shadow" style="left:613px;top:1070px;width:446px;height:210px">
    <div class="flap" style="height:75px"><div class="brand" style="top:22px">Meridian Freight Group</div></div>
  </div>
</section>

<section class="section s-folder">
  <div class="abs folder-back shadow">
    <div class="tiny">Meridian Freight Group<br>75 Beacon Road, Lakeview, ON X0X 0A0<br>555-010-4418 · info@meridianfreight.example</div>
  </div>
  <div class="abs folder-front shadow">
    <div class="brand">Meridian Freight Group</div>
    <div class="web">WWW.MERIDIANFREIGHT.EXAMPLE</div>
    <div class="band"></div>
  </div>
</section>

<section class="section s-notebook">
  <div class="abs notebook-open shadow">
    <div class="page"><div class="brand">Meridian Freight Group</div></div>
    <div class="page"></div>
  </div>
  <div class="abs notebook-cover shadow">
    <div class="brand light">Meridian Freight Group</div>
    <div class="elastic"></div>
    <div class="web">www.meridianfreight.example</div>
  </div>
</section>

</body>
</html>
```